Hardcore nerd needs to stand out in a sea of dull Defence business cards

Wombarra Devices is a new Australian consulting engineering company that turns research and theory into practical systems. No evangelistic fluff, just mathematics and physics into electronic and optical circuits for consumer products, scientific research or Defence applications.

We already have a recognised logo (provided) which is often dark blue/black on a light background but we're open to other combinations. (Us engineers tend to have limited aesthetic imagination :)

Some of our recent products have included:
* Instrumentation for electrical testing,
* Radar jammers,
* GPS antenna design,
* Satellite tracking systems,
* High power lasers

We're open to both single and double-sided designs - happy to be convinced either way.

P.S. Another group is working on the web page, so - alas - our web site is currently of no use for images/ideas...

Target Market(s)

Engineering managers,
Scientists

Contact Information for Business Card

Dr Colin Harte
R&D Engineer

colin@wombarradevices.com.au
0427 563 710

PO Box XXX (to be confirmed)
Kelsby ACT 2917
Australia

Font styles to use
Serif
Sans Serif

Colors

Designer to choose colors to be used in the design.

Requirements
Must have
• My contact details!
• I've had many (great) "bold and plain" designs submitted already, so feel free to be artistically creative :)
• Happy to take advice re fonts/colours/printability etc.
Nice to have
• I'm not sure if "lists" are more at home on a CV than a business card, but representative services include:
• Applied electromagnetics
• RF and high speed electronics
• Signal and image processing
• Electro-optical and laser systems
• Concept-to-prototype design services
• If you're considering double sided cards, then often measuring/alignment grids/rulers feature on the back of similar cards.
• e.g. https://www.veltranoptics.example/newgrouppage9.cfm?objectgroup_id=4183
• https://www.veltranoptics.example/newgrouppage9.cfm?objectgroup_ID=4185
• ..or even a "Smith chart" (google will return lots)
• Generic images to represent a capability might work - googling images associated with keyword for each of these areas might help:
• - "passive radar", "phased array", "fdtd", "vircator"
• RF and high speed electronic design
• - "smith chart", "microstrip circuits", "dimensioned drawing", "electronic schematic"
• - "dft", "iir filter"
• - "optical cavity". "laser energy level diagram"
• Background/watermarked images outlines/wireframes/schematics would probably look OK.
Should not have
• If a list of projects/services is provided, it is important not to make the client feel that this is "all" the company can do. Engineering design is a creative discipline (like graphics :)
• Please, no stock "military" snaps like planes, missiles, etc!

```html
<!DOCTYPE html>
<html lang="en">
<head>
<meta charset="utf-8">
<title>Wombarra Devices – Business Card</title>
<link rel="stylesheet" href="https://fonts.googleapis.com/css2?family=Roboto:wght@400;700&family=Roboto+Condensed:wght@400;700&display=swap">
<style>
  :root {
    --navy: #14297c;
    --navy-deep: #0f2065;
    --navy-faint: #1a3189;
    --ink-grey: #5a5d66;
    --paper: #ffffff;
    --stage: #3a3a3a;
    --stage-edge: #222222;
  }
  * { box-sizing: border-box; margin: 0; padding: 0; }
  html, body { width: 1200px; height: 900px; overflow: hidden; }
  body {
    background: radial-gradient(ellipse at 50% 40%, var(--stage), var(--stage-edge));
    font-family: "Roboto", Arial, sans-serif;
    position: relative;
  }
  .card {
    position: absolute;
    left: 250px;
    width: 700px;
    height: 400px;
    overflow: hidden;
    box-shadow: 0 10px 30px rgba(0,0,0,.45);
  }
  .card--front { top: 40px; background: var(--paper); }
  .card--back { top: 465px; background: var(--navy); }

  /* front */
  .brand {
    position: absolute; left: 42px; top: 48px;
    display: flex; align-items: center; gap: 12px;
  }
  .brand__dot { width: 58px; height: 58px; border-radius: 50%; background: var(--navy); }
  .brand__name {
    font-family: "Roboto Condensed", Arial, sans-serif;
    font-weight: 700; font-size: 30px; color: var(--navy);
    text-transform: uppercase; line-height: 1;
  }
  .divider {
    position: absolute; left: 80px; right: 52px; top: 172px;
    height: 1.5px; background: var(--navy);
  }
  .person { position: absolute; right: 52px; top: 98px; text-align: right; }
  .person__name {
    font-family: "Roboto Condensed", Arial, sans-serif;
    font-weight: 700; font-size: 31px; color: var(--navy);
    text-transform: uppercase; line-height: 1.05;
  }
  .person__role {
    font-family: "Roboto Condensed", Arial, sans-serif;
    font-size: 17px; color: var(--ink-grey); margin-top: 4px;
  }
  .contacts {
    position: absolute; left: 42px; top: 200px;
    list-style: none;
    font-family: "Roboto Condensed", Arial, sans-serif;
    font-size: 15px; color: var(--ink-grey);
  }
  .contacts li { display: flex; align-items: center; gap: 8px; height: 22px; }
  .contacts svg { width: 11px; height: 11px; fill: var(--navy); flex: none; }
  .contacts .web { color: var(--navy); font-weight: 700; }
  .address {
    position: absolute; right: 52px; top: 196px; text-align: left;
    font-family: "Roboto Condensed", Arial, sans-serif;
    font-size: 19px; line-height: 1.35; color: var(--ink-grey);
  }
  .band { position: absolute; left: 0; bottom: 0; width: 700px; height: 120px; }

  /* back */
  .pattern-field {
    position: absolute; inset: 0;
    background: linear-gradient(135deg, var(--navy-faint), var(--navy) 55%, var(--navy-deep));
  }
  .back-copy {
    position: absolute; right: 60px; top: 110px; text-align: right; color: var(--paper);
  }
  .back-copy__name {
    font-family: "Roboto", Arial, sans-serif;
    font-weight: 700; font-size: 46px; letter-spacing: 2px;
    text-transform: uppercase; line-height: 1.05;
  }
  .back-copy__services {
    margin-top: 26px;
    font-family: "Roboto Condensed", Arial, sans-serif;
    font-size: 16px; line-height: 1.5; opacity: .92;
  }
</style>
</head>
<body>

<section class="card card--front" aria-label="Business card front">
  <div class="brand">
    <span class="brand__dot"></span>
    <span class="brand__name">Wombarra Devices</span>
  </div>

  <div class="person">
    <p class="person__name">Dr Colin Harte</p>
    <p class="person__role">R&amp;D Engineer</p>
  </div>

  <div class="divider"></div>

  <ul class="contacts">
    <li>
      <svg viewBox="0 0 12 12"><path d="M2.5 1 L4.5 1 L5.2 3.6 L4 4.6 Q5 7 7.4 8 L8.4 6.8 L11 7.5 L11 9.5 Q10.5 11 9 11 Q1 10 1 3 Q1 1.5 2.5 1 Z"/></svg>
      <span>0427 563 710</span>
    </li>
    <li>
      <svg viewBox="0 0 12 12"><path d="M1 2.5 H11 V9.5 H1 Z M1.8 3.3 V8.7 H10.2 V3.3 L6 6.4 Z M2.6 3.3 L6 5.6 L9.4 3.3 Z" fill-rule="evenodd"/></svg>
      <span>colin@wombarradevices.com.au</span>
    </li>
    <li>
      <svg viewBox="0 0 12 12"><circle cx="6" cy="6" r="5"/><path d="M1 6 H11 M6 1 Q3 6 6 11 Q9 6 6 1" stroke="#fff" stroke-width=".8" fill="none"/></svg>
      <span class="web">www.wombarradevices.com.au</span>
    </li>
  </ul>

  <address class="address" style="font-style: normal;">
    PO Box XXX (to be confirmed)<br>
    Kelsby ACT 2917 Australia
  </address>

  <svg class="band" viewBox="0 0 700 120" preserveAspectRatio="none" aria-hidden="true">
    <path d="M0 30 L340 78 Q362 81 376 92 L400 108 Q412 116 430 117 L700 120 L700 120 L0 120 Z" fill="var(--navy)"/>
    <path d="M0 14 L350 62" stroke="var(--navy)" stroke-width="4" fill="none"/>
  </svg>
</section>

<section class="card card--back" aria-label="Business card back">
  <div class="pattern-field" role="img" aria-label="Faint repeating company mark pattern across the navy background"></div>
  <div class="back-copy">
    <p class="back-copy__name">Wombarra Devices</p>
    <p class="back-copy__services">
      Instrumentation for electrical testing, | Radar jammers,<br>
      GPS antenna design, | Satellite tracking systems, | High power lasers
    </p>
  </div>
</section>

</body>
</html>
```